Water ATM Card

Need a design for water ATM cards. Size of card is 3.375 x 2.125 inch
On the Front include the Cedar hollow Logo.
Bottom right corner should have Price $100
On the Back
This card is to be used to access water refills at any Cedar Hollow Water Vending Machines.
Please contact (869) 418 2930 or (869) 534 1276 or email clearflowbox@mailvista.example for any assistance or recharging of card.

```html
<!DOCTYPE html>
<html lang="en">
<head>
<meta charset="utf-8">
<title>Cedar Hollow Water Card</title>
<link rel="stylesheet" href="https://fonts.googleapis.com/css2?family=Poppins:wght@400;500;600;700;800&display=swap">
<style>
  :root {
    --backdrop: #c9c9c9;
    --green-light: #8cc63f;
    --green-deep: #3a9e3a;
    --blue-bright: #1ea7ee;
    --blue-mid: #1a73e0;
    --blue-deep: #1748c4;
    --blue-text: #1a5fbf;
    --white: #ffffff;
  }
  html, body {
    margin: 0;
    width: 1200px;
    height: 900px;
    overflow: hidden;
    background: var(--backdrop);
    font-family: "Poppins", sans-serif;
  }
  .stage { position: relative; width: 1200px; height: 900px; }
  .card {
    position: absolute;
    width: 560px;
    height: 352px;
    border-radius: 26px;
    overflow: hidden;
    box-shadow: 0 10px 24px rgba(0,0,0,.28);
  }
  .card-back { left: 110px; top: 80px; }
  .card-front { left: 530px; top: 470px; background: var(--white); }
  .card-art { position: absolute; inset: 0; width: 100%; height: 100%; }

  .back-notice {
    position: absolute; left: 0; right: 0; top: 42px;
    margin: 0; text-align: center;
    color: var(--white); font-weight: 800; font-size: 19px;
    line-height: 1.3; letter-spacing: .5px; text-transform: uppercase;
  }
  .back-contact {
    position: absolute; left: 0; right: 0; top: 166px;
    text-align: center; color: var(--white);
  }
  .contact-label { margin: 0; font-weight: 700; font-size: 14px; }
  .contact-phones { margin: 2px 0 0; font-weight: 700; font-size: 27px; line-height: 1.2; }
  .contact-phones .joiner, .contact-email .joiner { font-weight: 400; font-size: 15px; }
  .contact-email { margin: 0; font-weight: 700; font-size: 24px; line-height: 1.25; }
  .contact-note { margin: 2px 0 0; font-weight: 400; font-size: 15px; }

  .brand-name {
    position: absolute; left: 60px; top: 150px; margin: 0;
    color: var(--blue-text); font-weight: 800; font-size: 40px;
    letter-spacing: 1px; text-transform: uppercase;
  }
  .price-tag {
    position: absolute; right: 38px; bottom: 36px; margin: 0;
    color: var(--white); font-weight: 700; font-size: 24px;
  }
</style>
</head>
<body>
<main class="stage">

  <section class="card card-back" aria-label="Card back">
    <svg class="card-art" viewBox="0 0 560 352" preserveAspectRatio="none" aria-hidden="true">
      <defs>
        <linearGradient id="backGreen" x1="1" y1="0" x2="0" y2="1">
          <stop offset="0" stop-color="var(--green-light)"/>
          <stop offset="1" stop-color="var(--green-deep)"/>
        </linearGradient>
        <linearGradient id="backBlue" x1="1" y1="0" x2="0" y2="1">
          <stop offset="0" stop-color="var(--blue-bright)"/>
          <stop offset="1" stop-color="var(--blue-deep)"/>
        </linearGradient>
      </defs>
      <rect width="560" height="352" fill="url(#backGreen)"/>
      <path d="M0 250 C140 330 260 160 560 70 L560 352 L0 352 Z" fill="#5fc3e8" opacity=".45"/>
      <path d="M0 290 C160 330 300 150 560 110 L560 352 L0 352 Z" fill="url(#backBlue)"/>
      <path d="M0 320 C180 300 330 190 560 150" stroke="#ffffff" stroke-opacity=".25" stroke-width="6" fill="none"/>
    </svg>
    <p class="back-notice">This card is to be used to<br>access water refills at any Cedar Hollow<br>water vending machines</p>
    <div class="back-contact">
      <p class="contact-label">Please contact</p>
      <p class="contact-phones">(869) 418 2930 <span class="joiner">or</span> (869) 534 1276</p>
      <p class="contact-email"><span class="joiner">or</span> clearflowbox@mailvista.example</p>
      <p class="contact-note">for any assistance or recharging of card</p>
    </div>
  </section>

  <section class="card card-front" aria-label="Card front">
    <svg class="card-art" viewBox="0 0 560 352" preserveAspectRatio="none" aria-hidden="true">
      <defs>
        <linearGradient id="frontBlue" x1="1" y1="0" x2="0" y2="1">
          <stop offset="0" stop-color="var(--blue-mid)"/>
          <stop offset=".6" stop-color="var(--blue-bright)"/>
          <stop offset="1" stop-color="#7fd6f7"/>
        </linearGradient>
      </defs>
      <path d="M0 250 C200 300 360 230 430 140 C470 90 520 70 560 60 L560 352 L0 352 Z" fill="#bfe9fb" opacity=".6"/>
      <path d="M0 285 C210 330 380 260 450 160 C490 110 530 95 560 90 L560 352 L0 352 Z" fill="url(#frontBlue)"/>
      <path d="M60 352 C250 320 380 260 470 170 C510 130 540 120 560 118" stroke="#0d3fb8" stroke-opacity=".45" stroke-width="14" fill="none"/>
      <path d="M0 300 C220 330 390 250 460 150" stroke="#ffffff" stroke-opacity=".35" stroke-width="4" fill="none"/>
    </svg>
    <h1 class="brand-name">Cedar Hollow</h1>
    <p class="price-tag">PRICE $100</p>
  </section>

</main>
</body>
</html>
```